Business card for law firm

Need business card for new law firm. Think confident, authoritative, conservative, but not stuffy or old-fashioned.

Contact Information for Business Card

Content for card - logo (uploaded), plus the following:

Paul Whitcombe (larger font)
Managing Partner (larger font, but not as large as name)
Level 9, 7 Ferris Lane
Sydney NSW 2000
Main Tel 02 9364 2710
Direct Tel 02 8472 3159
Email paul@qvlegal.com.au
www.qvlegal.com.au

Letterhead design should include logo plus:
Level 9, 7 Ferris Lane
Sydney NSW 2000
Tel 02 8472 3159
www.qvlegal.com.au

```html
<!DOCTYPE html>
<html lang="en">
<head>
<meta charset="utf-8">
<title>Quayvale Legal – Business Card</title>
<link href="https://fonts.googleapis.com/css2?family=Cinzel:wght@700&family=Raleway:wght@400;500&display=swap" rel="stylesheet">
<style>
  :root {
    --navy: #1c2566;
    --navy-deep: #121a4d;
    --navy-light: #26307a;
    --ink: #0d0f1c;
    --paper: #ffffff;
    --paper-shade: #e9eaee;
    --backdrop: #3a3b3f;
    --backdrop-dark: #1e1f22;
    --silver: #e4e6ee;
  }
  * { box-sizing: border-box; margin: 0; padding: 0; }
  html, body { width: 1200px; height: 900px; overflow: hidden; }
  body {
    background: radial-gradient(ellipse at center, var(--backdrop) 0%, var(--backdrop-dark) 100%);
    font-family: 'Raleway', sans-serif;
    position: relative;
  }
  .card {
    position: absolute;
    left: 260px;
    width: 680px;
    height: 388px;
    border-radius: 22px;
    overflow: hidden;
    box-shadow: 0 14px 34px rgba(0,0,0,0.45);
  }
  .card--front {
    top: 40px;
    background: linear-gradient(135deg, var(--paper) 40%, var(--paper-shade) 100%);
  }
  .card--back {
    top: 472px;
    background: radial-gradient(ellipse at 50% 40%, var(--navy-light) 0%, var(--navy) 55%, var(--navy-deep) 100%);
  }
  .card__wave { position: absolute; inset: 0; width: 100%; height: 100%; }

  .firm-name {
    position: absolute;
    display: flex;
    align-items: center;
    gap: 14px;
    font-family: 'Raleway', sans-serif;
    font-weight: 500;
    line-height: 1;
    white-space: nowrap;
  }
  .firm-name__square { display: block; flex: none; }

  .card--front .firm-name {
    left: 40px; top: 62px;
    color: var(--navy);
    font-size: 32px;
  }
  .card--front .firm-name__square { width: 30px; height: 30px; background: var(--navy); }

  .card--back .firm-name {
    left: 0; right: 0; top: 140px;
    justify-content: center;
    color: var(--silver);
    font-size: 50px;
  }
  .card--back .firm-name__square { width: 44px; height: 44px; background: var(--silver); }

  .back__web {
    position: absolute; left: 0; right: 0; top: 270px;
    text-align: center;
    color: var(--silver);
    font-size: 17px;
    letter-spacing: 5px;
  }

  .divider {
    position: absolute;
    left: 40px; right: 40px; top: 176px;
    height: 2px;
    background: var(--navy);
  }
  .address {
    position: absolute;
    left: 40px; top: 190px;
    color: var(--navy);
    font-size: 16px;
    line-height: 22px;
    font-weight: 500;
  }
  .person {
    position: absolute;
    right: 40px; top: 114px;
    text-align: right;
    color: var(--navy);
  }
  .person__name {
    font-family: 'Cinzel', serif;
    font-weight: 700;
    font-size: 25px;
    letter-spacing: 0.5px;
  }
  .person__role { font-size: 16px; font-weight: 500; margin-top: 2px; }

  .contacts {
    position: absolute;
    right: 40px; top: 192px;
    list-style: none;
    color: var(--navy);
    text-align: right;
  }
  .contacts li {
    display: flex;
    justify-content: flex-end;
    align-items: center;
    gap: 9px;
    font-size: 17px;
    font-weight: 500;
    line-height: 25px;
  }
  .contacts li:nth-child(-n+2) { font-size: 19px; }
  .contacts svg { width: 14px; height: 14px; flex: none; }
</style>
</head>
<body>

<section class="card card--front" aria-label="Business card front">
  <svg class="card__wave" viewBox="0 0 680 388" preserveAspectRatio="none" aria-hidden="true">
    <path d="M0,252 C110,270 170,320 260,352 C330,376 400,384 470,388 L0,388 Z" fill="var(--navy)"/>
    <path d="M0,244 C110,262 175,312 262,344 C332,368 402,378 475,388" fill="none" stroke="var(--ink)" stroke-width="5"/>
  </svg>

  <div class="firm-name">
    <span class="firm-name__square" aria-hidden="true"></span>
    <span class="firm-name__text">Quayvale Legal</span>
  </div>

  <div class="divider"></div>

  <div class="person">
    <div class="person__name">PAUL WHITCOMBE</div>
    <div class="person__role">Managing Partner</div>
  </div>

  <p class="address">Level 9, 7 Ferris Lane<br>Sydney NSW 2000</p>

  <ul class="contacts">
    <li>02 9364 2710
      <svg viewBox="0 0 16 16"><path d="M4 1.5 L6.3 4.5 L5 6.2 C5.8 8 7.8 10 9.8 11 L11.5 9.7 L14.5 12 L13 14.5 C7 14 2 9 1.5 3 Z" fill="none" stroke="currentColor" stroke-width="1.4" stroke-linejoin="round"/></svg>
    </li>
    <li>02 8472 3159
      <svg viewBox="0 0 16 16"><rect x="4" y="1" width="8" height="14" rx="1.5" fill="none" stroke="currentColor" stroke-width="1.4"/><line x1="7" y1="12.5" x2="9" y2="12.5" stroke="currentColor" stroke-width="1.4"/></svg>
    </li>
    <li>paul@qvlegal.com.au
      <svg viewBox="0 0 16 16"><rect x="1" y="3.5" width="14" height="9.5" fill="none" stroke="currentColor" stroke-width="1.4"/><path d="M1 3.5 L8 9 L15 3.5" fill="none" stroke="currentColor" stroke-width="1.4"/></svg>
    </li>
    <li>www.qvlegal.com.au
      <svg viewBox="0 0 16 16"><circle cx="8" cy="8" r="6.5" fill="none" stroke="currentColor" stroke-width="1.3"/><ellipse cx="8" cy="8" rx="3" ry="6.5" fill="none" stroke="currentColor" stroke-width="1.1"/><line x1="1.5" y1="8" x2="14.5" y2="8" stroke="currentColor" stroke-width="1.1"/><line x1="2.5" y1="4.8" x2="13.5" y2="4.8" stroke="currentColor" stroke-width="1"/><line x1="2.5" y1="11.2" x2="13.5" y2="11.2" stroke="currentColor" stroke-width="1"/></svg>
    </li>
  </ul>
</section>

<section class="card card--back" aria-label="Business card back">
  <div class="firm-name">
    <span class="firm-name__square" aria-hidden="true"></span>
    <span class="firm-name__text">Quayvale Legal</span>
  </div>
  <p class="back__web">www.qvlegal.com.au</p>
</section>

</body>
</html>
```